RW Framewell Inc Business cards

We need business cards using our existing logo but slightly modified. Right now the logo says RW Loadbearing Masonry. We want to keep the RW part of the design, but replace the Structural Concrete portion with "FRAMEWELL". Please see the attached file.
Ideally this would be a blank template so we can add Different Names, titles, and phone numbers later.
On the one side we want only the logo and on the other side the detail. I'm attaching an example for you to see.
Please reach out with any other questions. Our address and other details will be given out once we find a design we like.

Target Market(s)

Construction Industry

```html
<!DOCTYPE html>
<html lang="en">
<head>
<meta charset="utf-8">
<title>RW Framewell Inc – Business Cards</title>
<link rel="stylesheet" href="https://fonts.googleapis.com/css2?family=Roboto:wght@400;500;700;900&display=swap">
<style>
  :root {
    --stage: #232323;
    --card-white: #ffffff;
    --brand-blue: #1274bf;
    --brand-blue-deep: #0e6ab0;
    --ink: #2b2b2b;
    --muted: #444444;
    --rule: #8a8a8a;
  }
  * { box-sizing: border-box; margin: 0; padding: 0; }
  html, body {
    width: 1200px; height: 1200px; overflow: hidden;
    background: var(--stage);
    font-family: "Roboto", Arial, sans-serif;
  }
  .stage {
    position: relative; width: 1200px; height: 1200px;
    display: flex; align-items: center; justify-content: center; gap: 60px;
  }
  .card {
    width: 400px; height: 700px; border-radius: 30px;
    position: relative; overflow: hidden;
  }
  /* Front: details side */
  .card--front {
    background: var(--card-white);
    display: flex; flex-direction: column; align-items: center;
    color: var(--ink);
  }
  .front__wordmark {
    margin-top: 150px;
    font-size: 130px; font-weight: 900; letter-spacing: 4px;
    color: var(--brand-blue); line-height: 1;
  }
  .front__name {
    margin-top: 160px;
    font-size: 26px; font-weight: 700; letter-spacing: 1px;
    color: var(--brand-blue);
  }
  .front__title {
    margin-top: 4px; font-size: 17px; color: var(--muted);
  }
  .rule {
    width: 260px; height: 1.5px; background: var(--rule);
    margin: 14px 0;
  }
  .front__address {
    text-align: center; font-size: 17px; line-height: 1.35; color: var(--ink);
  }
  .contact-list {
    list-style: none; font-size: 17px; line-height: 1.45; color: var(--ink);
  }
  .contact-list li { display: flex; align-items: center; gap: 8px; }
  .contact-list svg { width: 14px; height: 14px; flex: none; }

  /* Back: logo side */
  .card--back {
    background: var(--brand-blue);
  }
  .back__texture {
    position: absolute; inset: 0 0 180px 0;
    background: linear-gradient(180deg, #1679c4 0%, #1172bd 70%, rgba(18,116,191,0) 100%);
  }
  .back__logo {
    position: absolute; left: 0; right: 0; bottom: 80px;
    text-align: center; color: var(--card-white);
  }
  .back__wordmark {
    font-size: 96px; font-weight: 900; letter-spacing: 3px; line-height: 1;
  }
  .back__tagline {
    margin-top: 10px; font-size: 14px; font-weight: 500;
    letter-spacing: 9px; padding-left: 9px;
  }
</style>
</head>
<body>
<main class="stage">
  <section class="card card--front" aria-label="Business card, details side">
    <div class="front__wordmark">RW</div>
    <h1 class="front__name">JORDAN HALE</h1>
    <p class="front__title">Owner/CEO</p>
    <div class="rule"></div>
    <address class="front__address">418 Quarry Bend Road<br>Millbrook 7046</address>
    <div class="rule"></div>
    <ul class="contact-list">
      <li>
        <svg viewBox="0 0 14 14" aria-hidden="true"><rect x="3.5" y="1" width="7" height="12" rx="1.5" fill="none" stroke="#1274bf" stroke-width="1.4"/><circle cx="7" cy="11" r="0.8" fill="#1274bf"/></svg>
        555-014-2290
      </li>
      <li>
        <svg viewBox="0 0 14 14" aria-hidden="true"><path d="M3 1.5l2.2 2.6-1.2 1.4c.8 1.8 2 3 3.8 3.8l1.4-1.2 2.6 2.2-1.3 2c-4.5-.5-8.4-4.4-8.8-8.8z" fill="#1274bf"/></svg>
        555-013-7718
      </li>
      <li>
        <svg viewBox="0 0 14 14" aria-hidden="true"><rect x="1" y="3" width="12" height="8" fill="#1274bf"/><path d="M1 3l6 4.5L13 3" fill="none" stroke="#fff" stroke-width="1"/></svg>
        info@rwframewell.com
      </li>
      <li>
        <svg viewBox="0 0 14 14" aria-hidden="true"><circle cx="7" cy="7" r="6" fill="#1274bf"/><path d="M1 7h12M7 1c2.5 3 2.5 9 0 12M7 1c-2.5 3-2.5 9 0 12" fill="none" stroke="#fff" stroke-width="0.8"/></svg>
        www.rwframewell.com
      </li>
    </ul>
  </section>

  <section class="card card--back" aria-label="Business card, logo side">
    <div class="back__texture" role="img" aria-label="Faint repeating brand pattern across the blue background"></div>
    <div class="back__logo">
      <div class="back__wordmark">RW</div>
      <div class="back__tagline">FRAMEWELL</div>
    </div>
  </section>
</main>
</body>
</html>
```